Composite decking sales poster

Poster advertising our brand of decking and our industry-best warranty.
Poster dimensions 1200mm wide x 400mm high.
50 Year Stain and Fade Warranty.
Ultra-Low Maintenance.
Environmentally Friendly Made from Recycled Materials.
Website: https://plankhavenboards.com.au
Phone: 1300 947 352
Must list website, phone number and logos.

```html
<!DOCTYPE html>
<html lang="en">
<head>
<meta charset="utf-8">
<title>PlankHaven Boards – Decking Poster</title>
<link rel="stylesheet" href="https://fonts.googleapis.com/css2?family=Montserrat:ital,wght@0,500;0,600;0,700;1,700;1,800;1,900&family=Open+Sans:wght@400;500&display=swap">
<style>
  :root {
    --page: #e1e1e1;
    --white: #ffffff;
    --ink: #3a3a3c;
    --brand-blue: #2f6db4;
    --deck-light: #9c8c8a;
    --deck-mid: #7a6664;
    --deck-dark: #5c4644;
    --bar-grey: #4b4b4d;
    --badge-fill: #6f6760;
    --headline-shadow: #1f2a3c;
  }
  * { margin: 0; padding: 0; box-sizing: border-box; }
  html, body { width: 1200px; height: 510px; overflow: hidden; background: var(--page); }
  .poster {
    position: absolute; left: 42px; top: 69px; width: 1116px; height: 372px;
    overflow: hidden; box-shadow: 0 2px 6px rgba(0,0,0,.35);
    font-family: "Montserrat", sans-serif;
  }
  .deck-photo {
    position: absolute; inset: 0;
    background: linear-gradient(100deg, var(--deck-light) 0%, var(--deck-mid) 45%, var(--deck-dark) 100%);
  }
  .header-curve { position: absolute; left: 0; top: 0; width: 1116px; height: 120px; }
  .brand { position: absolute; left: 40px; top: 16px; display: flex; align-items: center; gap: 14px; }
  .brand-mark { width: 36px; height: 36px; background: var(--brand-blue); }
  .brand-name { font-weight: 700; font-size: 38px; color: var(--ink); letter-spacing: -0.5px; }
  .website { position: absolute; left: 125px; top: 72px; font-size: 14px; font-weight: 700; font-style: italic; color: var(--ink); }
  .headline {
    position: absolute; left: 431px; top: 76px; color: var(--white);
    font-weight: 900; font-style: italic; font-size: 45px; line-height: 42px; letter-spacing: -0.5px;
    text-shadow: 3px 3px 0 var(--headline-shadow); white-space: nowrap;
  }
  .project-photo {
    position: absolute; left: 27px; top: 156px; width: 352px; height: 188px;
    border: 4px solid #c9c5c3; border-radius: 0 70px 0 40px;
    background: linear-gradient(90deg, #6b4a32 0%, #a07c5c 35%, #d9d3cb 60%, #8c9a7a 85%, #6f6458 100%);
  }
  .feature-icon { position: absolute; top: 214px; width: 72px; height: 72px; border-radius: 10px; background: var(--white); }
  .feature-icon svg { width: 72px; height: 72px; }
  .icon-eco { left: 439px; }
  .icon-maintain { left: 652px; }
  .feature-text { position: absolute; top: 298px; color: var(--white); font-weight: 600; font-size: 14.5px; line-height: 21px; white-space: nowrap; }
  .feature-low { left: 418px; width: 122px; white-space: normal; text-align: center; }
  .feature-env { left: 591px; }
  .feature-divider { position: absolute; left: 564px; top: 301px; width: 2px; height: 35px; background: var(--white); }
  .phone-bar {
    position: absolute; left: 885px; top: 192px; width: 231px; height: 33px; background: var(--bar-grey);
    color: var(--white); font-family: "Open Sans", sans-serif; font-weight: 500; font-size: 29px; line-height: 33px;
    padding-left: 21px; white-space: nowrap;
  }
  .phone-circle {
    position: absolute; left: 852px; top: 185px; width: 44px; height: 44px; border-radius: 50%;
    background: var(--white); border: 3px solid var(--bar-grey);
  }
  .phone-circle svg { width: 38px; height: 38px; }
  .badge {
    position: absolute; top: 243px; width: 99px; height: 100px; background: var(--badge-fill);
    border: 3px solid var(--white); outline: 2px solid var(--bar-grey); border-radius: 4px;
    color: var(--white); font-family: "Open Sans", sans-serif; text-align: center;
  }
  .badge > * { position: absolute; left: 0; right: 0; white-space: nowrap; }
  .badge-fifty { left: 880px; }
  .badge-life { left: 992px; }
  .badge-number { top: 6px; font-size: 52px; font-weight: 500; line-height: 52px; }
  .badge-number small { font-size: 7px; }
  .badge-label { top: 66px; font-size: 10.5px; line-height: 13px; }
  .badge-fine { top: 83px; font-size: 5.5px; line-height: 8px; }
  .badge-ribbon {
    top: 31px; left: -3px; right: -3px; background: var(--white); color: var(--badge-fill);
    font-size: 20px; line-height: 25px;
  }
</style>
</head>
<body>
<div class="poster">
  <div class="deck-photo" role="img" aria-label="Close-up of brown composite deck boards"></div>

  <svg class="header-curve" viewBox="0 0 1116 120" aria-hidden="true">
    <path d="M0 0 H700 C560 8 470 30 430 70 C400 100 370 106 320 106 H0 Z" fill="#8d857f" opacity=".85"/>
    <path d="M0 0 H680 C540 4 450 22 410 60 C380 90 350 98 310 98 H0 Z" fill="var(--white)"/>
  </svg>

  <div class="brand">
    <span class="brand-mark"></span>
    <span class="brand-name">PlankHaven</span>
  </div>
  <div class="website">plankhavenboards.com.au</div>

  <h1 class="headline">INDUSTRY’S BEST DECKING<br>WITH BEST WARRANTY</h1>

  <div class="project-photo" role="img" aria-label="Covered timber deck with outdoor lounge, barbecue and dining set"></div>

  <div class="feature-icon icon-eco">
    <svg viewBox="0 0 72 72" aria-hidden="true">
      <path d="M18 40 A19 19 0 0 1 52 24" fill="none" stroke="var(--brand-blue)" stroke-width="4"/>
      <path d="M54 32 A19 19 0 0 1 20 48" fill="none" stroke="var(--brand-blue)" stroke-width="4"/>
      <path d="M36 22 C46 30 46 44 36 50 C26 44 26 30 36 22 Z" fill="var(--brand-blue)"/>
      <path d="M36 30 V50" stroke="var(--white)" stroke-width="2"/>
    </svg>
  </div>
  <div class="feature-icon icon-maintain">
    <svg viewBox="0 0 72 72" aria-hidden="true">
      <rect x="24" y="12" width="20" height="8" fill="var(--brand-blue)"/>
      <rect x="32" y="18" width="6" height="18" fill="var(--brand-blue)"/>
      <rect x="12" y="32" width="48" height="7" rx="3" fill="var(--brand-blue)"/>
      <path d="M27 44 H45 L36 58 Z" fill="var(--brand-blue)"/>
      <rect x="33" y="38" width="6" height="8" fill="var(--brand-blue)"/>
    </svg>
  </div>

  <p class="feature-text feature-low">ULTRA-LOW MAINTENANCE</p>
  <span class="feature-divider"></span>
  <p class="feature-text feature-env">ENVIRONMENTALLY FRIENDLY<br>Made from Recycled Materials</p>

  <div class="phone-bar">1300 947 352</div>
  <div class="phone-circle">
    <svg viewBox="0 0 24 24" aria-hidden="true">
      <path d="M7 4 L10 8 L8.5 10 C9.5 12.5 11.5 14.5 14 15.5 L16 14 L20 17 L18 20 C11 20 4 13 4 6 Z" fill="var(--ink)"/>
    </svg>
  </div>

  <div class="badge badge-fifty">
    <div class="badge-number">50<small>Year</small></div>
    <div class="badge-label">Stain and Fade</div>
    <div class="badge-fine">Limited Residential Warranty</div>
  </div>
  <div class="badge badge-life">
    <div class="badge-ribbon">Lifetime</div>
    <div class="badge-label">Performance</div>
    <div class="badge-fine">Limited Residential Warranty</div>
  </div>
</div>
</body>
</html>
```